Business card design for new eCommerce site focusing on integrity and strong businsess tactics

We need a business card that will stand out and be memorable. Something with color that matches our company logo colors. Think high end version of Pactivo. There are 2 logos provided. The parent company is called Amber Ledge Partners and we are presenting a new and very exciting eCommerce site called BrightHarborTrade.example.

Target Market(s)

Our target markets are in the Activities, Food and Beverage, Health and Beauty

Industry/Entity Type

Marketing

Contact Information for Business Card

We have 4 members that need cards...I will provide all info to the winner of the design contest
Business Address is
4870 West 63rd Avenue, Suite C207
Phoenix AZ 85731

Font styles to use
Serif
Sans Serif

Colors

Designer to choose colors to be used in the design.

Requirements
Must have
• The card must be memorable...should be unique in design but must exude integrity and be playful .
• I have provided several colors or our parent company...please feel free to use which ever
Nice to have
• I will leave this up to you. Feel free to use other images of your choosing that wraps around our client.....Activities, Dining, Health, Beauty
Should not have
• just dont be boring

```html
<!DOCTYPE html>
<html lang="en">
<head>
<meta charset="utf-8">
<title>BrightHarborTrade.example business card</title>
<link rel="stylesheet" href="https://fonts.googleapis.com/css2?family=Mulish:wght@400;700&family=Arimo:wght@700&display=swap">
<style>
  :root {
    --backdrop: #2b2b2b;
    --card-white: #f4f4f4;
    --brand-blue: #2a78a8;
    --brand-green: #79bc3a;
    --text-grey: #4a4a4a;
    --white: #ffffff;
  }
  * { margin: 0; padding: 0; box-sizing: border-box; }
  html, body { width: 1200px; height: 960px; overflow: hidden; }
  body { background: var(--backdrop); font-family: "Mulish", sans-serif; position: relative; }

  .card { position: absolute; width: 600px; height: 343px; overflow: hidden; }
  .card--front { left: 314px; top: 113px; background: var(--card-white); }
  .card--back { left: 311px; top: 472px; background: var(--brand-blue); }

  .swoosh { position: absolute; left: 0; top: 0; }

  .brand { position: absolute; left: 42px; top: 60px; display: flex; align-items: center; gap: 10px; }
  .brand__dot { width: 22px; height: 22px; border-radius: 50%; background: var(--brand-green); }
  .brand__name { font-size: 19px; font-weight: 700; color: var(--brand-blue); letter-spacing: -0.2px; }

  .contact { position: absolute; right: 36px; top: 130px; text-align: right; color: var(--text-grey); }
  .contact__name { font-size: 20px; font-weight: 700; color: var(--brand-blue); line-height: 24px; }
  .contact__role { font-size: 15px; color: var(--brand-green); line-height: 20px; margin-bottom: 8px; }
  .contact__address { font-size: 14.5px; line-height: 19px; margin-bottom: 9px; }
  .contact__line { font-size: 14.5px; line-height: 19.5px; display: flex; justify-content: flex-end; align-items: center; gap: 7px; }
  .contact__line svg { width: 13px; height: 13px; fill: var(--brand-blue); }

  .website { position: absolute; left: 28px; bottom: 15px; font-size: 13.5px; color: var(--white); letter-spacing: 0.2px; }

  .parent-brand { position: absolute; left: 0; right: 0; top: 0; bottom: 0; display: flex; flex-direction: column; align-items: center; justify-content: center; gap: 18px; }
  .parent-brand__dot { width: 58px; height: 58px; border-radius: 50%; border: 4px solid var(--white); }
  .parent-brand__name { font-family: "Arimo", sans-serif; font-weight: 700; font-size: 36px; color: var(--white); }
</style>
</head>
<body>
  <section class="card card--front">
    <svg class="swoosh" width="600" height="343" viewBox="0 0 600 343">
      <path d="M0,258 C150,300 340,336 600,302 L600,343 L0,343 Z" fill="var(--brand-blue)"/>
      <path d="M22,248 C170,288 360,322 572,304" fill="none" stroke="var(--brand-green)" stroke-width="4"/>
    </svg>

    <div class="brand">
      <span class="brand__dot"></span>
      <span class="brand__name">BrightHarborTrade.example</span>
    </div>

    <div class="contact">
      <div class="contact__name">DANA WHITFIELD</div>
      <div class="contact__role">CEO/FOUNDER</div>
      <div class="contact__address">4870 West 63rd Avenue<br>Suite C207, Phoenix AZ 85731</div>
      <div class="contact__line">555 210 4417
        <svg viewBox="0 0 24 24"><path d="M6.6 10.8a15.1 15.1 0 0 0 6.6 6.6l2.2-2.2a1 1 0 0 1 1-.25 11.4 11.4 0 0 0 3.6.57 1 1 0 0 1 1 1V20a1 1 0 0 1-1 1A17 17 0 0 1 3 4a1 1 0 0 1 1-1h3.5a1 1 0 0 1 1 1c0 1.25.2 2.45.57 3.57a1 1 0 0 1-.25 1z"/></svg>
      </div>
      <div class="contact__line">555 382 0926
        <svg viewBox="0 0 24 24"><path d="M7 1h10a2 2 0 0 1 2 2v18a2 2 0 0 1-2 2H7a2 2 0 0 1-2-2V3a2 2 0 0 1 2-2zm0 3v14h10V4z"/></svg>
      </div>
      <div class="contact__line">dana@brightharbortrade.example
        <svg viewBox="0 0 24 24"><path d="M2 5h20v14H2zm2 2v.5l8 5 8-5V7z"/></svg>
      </div>
    </div>

    <div class="website">www.brightharbortrade.example</div>
  </section>

  <section class="card card--back">
    <div class="parent-brand">
      <span class="parent-brand__dot"></span>
      <span class="parent-brand__name">Amber Ledge Partners</span>
    </div>
  </section>
</body>
</html>
```